Orthobiologic, StemCell, Bone Marrow Aspirate Device Distributor

We need a wordpress fully functioning website design for an innovative ortho-biologic, Bone Marrow Aspirate Device that extracts stem cells for orthopedic regenerative medical professionals. We also offer state of the art training in there office setting with licensed medical staff, a full service support team, and software for tracking patient outcome over time. We are an innovative company that prides itself on gold standard support. We will have other offerings on our website and would like a spot for "future" products. We would like to see designs that look professional, medical, and convey support, security, science, and innovation. We prefer shades of blue and red/orange. I particularly like the following websites that also sell the same device in order of preference:regenacelltherapy.comhttps://aspire-medical.eu/marrow-cellution/https://www.matrixbiosurgical.com/#emerging-solutions-in-healthcareElite2elite.comI have attached a few pictures of the device for reference

Target Market(s)

Orthopedics, Regenerative medicine doctors, Industry representatives, Hospitals

Industry/Entity Type

Medical Equipment

Coding

Coded - Design and coding required

Colors
3176b5
33a6d7
f37022
ec1f27

Requirements
Must have
• It must be able to have videos which I can supply, email, online ordering, and sfax. I have a domain name Coralweavesolutions.com . It must have a FAQ section which you can obtain some information from https://www.tolvenclinical.com/solutions#resources
• The device is manufactured by Dulmor and this is the link to the product page http://www.dulmor.com/quintadraw
• I am currently working on a custom logo and should be able to supply that in short order. I prefer shades of blue and red.
Nice to have
• I would love to have a graphic video as seen here: please see quinta draw vs bone marrow aspirate concentrate.
• https://www.tolvenclinical.com/solutions#competition
• I would pay considerably more to have something similar if it is at all possible
Should not have
• Nothing specific

```html
<!DOCTYPE html>
<html lang="en">
<head>
<meta charset="utf-8">
<title>Coralweave Solutions</title>
<link rel="stylesheet" href="https://fonts.googleapis.com/css2?family=Montserrat:wght@400;500;600;700;800&display=swap">
<style>
:root{
  --blue:#3176b5;
  --sky:#33a6d7;
  --bright:#1a8fe0;
  --panel:#0b7fd8;
  --ink:#1d1d1f;
  --text:#3a3a3a;
  --muted:#8a8f96;
  --pale:#d4e4f4;
  --navy:#0f2740;
  --dark:#141414;
  --white:#ffffff;
}
*{box-sizing:border-box;margin:0;padding:0}
html,body{width:1200px;height:5093px;overflow:hidden}
body{font-family:'Montserrat',sans-serif;color:var(--text);background:var(--white);position:relative}
.section-title{position:absolute;left:0;width:1200px;text-align:center;font-size:38px;font-weight:800;color:var(--ink);letter-spacing:.5px}
.arrow{position:absolute;width:36px;height:36px}
.btn{position:absolute;background:var(--blue);color:var(--white);font-weight:700;font-size:14px;display:flex;align-items:center;justify-content:center;letter-spacing:.3px}

/* header */
.site-header{position:absolute;top:0;left:0;width:1200px;height:113px;background:var(--white)}
.brand{position:absolute;left:113px;top:28px;display:flex;align-items:center;gap:12px}
.brand-dot{width:34px;height:34px;border-radius:50%;background:var(--sky);flex-shrink:0}
.brand-name{font-weight:800;font-size:20px;line-height:24px;color:var(--navy)}
.login{left:800px;top:18px;width:92px;height:34px;font-size:14px;background:var(--blue)}
.search{position:absolute;left:903px;top:18px;width:182px;height:34px;background:#e6e6e6;border:1px solid #d0d0d0;font-size:14px;color:#888;padding:8px 12px}
.search svg{position:absolute;right:10px;top:9px}
.main-nav{position:absolute;right:113px;top:72px;display:flex;gap:22px;font-size:15px;font-weight:700;color:var(--ink)}
.main-nav .active{color:var(--sky)}

/* hero */
.hero{position:absolute;top:113px;left:0;width:1200px;height:717px;overflow:hidden}
.hero-image{position:absolute;inset:0;background:linear-gradient(100deg,#0e2235 0%,#1a3a56 45%,#2d5674 70%,#16324c 100%)}
.hero h1{position:absolute;left:109px;top:196px;font-size:49px;font-weight:800;color:var(--white)}
.hero p{position:absolute;left:109px;top:262px;width:560px;font-size:17px;line-height:28px;color:var(--white)}
.hero .btn{left:109px;top:340px;width:152px;height:51px;font-size:16px}
.hero-curve{position:absolute;left:0;top:0}

/* products */
.product{position:absolute;width:300px;text-align:center}
.product-ring{width:190px;height:190px;border-radius:50%;border:4px solid var(--sky);margin:0 auto;background:var(--white)}
.product-ring div{width:100%;height:100%;border-radius:50%;background:radial-gradient(circle,#eef2f7 0%,#ffffff 70%)}
.product h3{margin-top:32px;font-size:21px;font-weight:700;line-height:28px;color:var(--text)}

/* who we are */
.who{position:absolute;top:1378px;left:0;width:1200px;height:546px;background:var(--pale)}
.video{position:absolute;left:109px;top:162px;width:478px;height:295px;border:5px solid var(--white);background:linear-gradient(160deg,#5f7382 0%,#9fb0bb 45%,#3c4d59 100%)}
.play{position:absolute;left:214px;top:122px}
.who-text{position:absolute;left:619px;top:162px;width:470px;font-size:12px;line-height:28px;color:#7b8794;text-align:justify}
.who .btn{left:619px;top:338px;width:120px;height:42px}

/* training */
.card{position:absolute;top:2125px;width:312px}
.card-photo{width:312px;height:224px}
.card-badge{position:absolute;left:0;top:194px;width:54px;height:54px;background:var(--white);border:2px solid var(--pale);display:flex;align-items:center;justify-content:center}
.card-badge span{width:24px;height:24px;background:var(--sky)}
.card h3{margin-top:44px;font-size:21px;font-weight:700;color:var(--ink)}
.card p{margin-top:12px;font-size:14px;line-height:28px;color:var(--text)}
.card .btn{position:static;margin-top:16px;width:130px;height:49px;gap:6px}

/* faq */
.faq{position:absolute;top:2669px;left:0;width:1200px;height:791px;background:var(--pale)}
.faq-item{position:absolute;left:200px;width:798px;background:var(--white);padding:22px 24px;box-shadow:0 1px 3px rgba(0,0,0,.05)}
.faq-item h4{width:680px;font-size:15px;font-weight:700;line-height:28px;color:var(--ink);text-transform:uppercase}
.faq-item p{margin-top:12px;width:600px;font-size:14px;line-height:28px;color:#555;text-align:justify}
.faq-more{margin-top:8px;font-size:13px;font-weight:700;color:var(--blue);display:flex;align-items:center;gap:6px}
.toggle{position:absolute;right:24px;width:46px;height:46px;border:2px solid #bcc4cc}
.faq .btn{left:492px;top:627px;width:214px;height:49px}

/* testimonials */
.quote{position:absolute;top:3657px;width:310px;border-left:3px solid var(--sky);padding-left:26px;font-size:12px;line-height:28px;color:#7b8794}
.person{position:absolute;top:3796px;display:flex;align-items:center;gap:28px}
.avatar{position:relative;width:130px;height:130px;border-radius:50%;background:linear-gradient(135deg,#d9dde2,#8c96a0);flex-shrink:0}
.avatar span{position:absolute;right:4px;bottom:6px;width:30px;height:30px;border-radius:6px;background:var(--sky)}
.person strong{display:block;font-size:14px;font-weight:700;color:var(--ink)}
.person em{display:block;margin-top:22px;font-style:normal;font-size:13px;color:var(--muted)}
.dots{position:absolute;top:4011px;left:563px;display:flex;gap:4px}
.dots i{width:11px;height:11px;border-radius:50%;background:#c9c9c9}
.dots i:first-child{background:var(--sky)}

/* contact */
.contact{position:absolute;top:4040px;left:0;width:1200px;height:642px;background:linear-gradient(120deg,#1f7fd0 0%,#3aa0e6 55%,#1a6fc0 100%);clip-path:polygon(0 0,690px 60px,1200px 60px,1200px 642px,0 642px)}
.touch{position:absolute;left:196px;top:4206px;color:var(--white)}
.touch h2{font-size:25px;font-weight:700;margin-bottom:40px}
.touch-row{position:relative;padding-left:28px;margin-bottom:36px;font-size:14px;line-height:28px}
.touch-row b{font-weight:700;display:block;color:#e4f1ff}
.touch-row svg{position:absolute;left:0;top:6px}
.subscribe{position:absolute;left:700px;top:4076px;width:474px;height:606px;background:var(--panel);padding:0 38px}
.subscribe h2{margin-top:46px;text-align:center;font-size:37px;font-weight:500;color:var(--white);letter-spacing:.5px;margin-bottom:34px}
.field{height:42px;border:1.5px solid var(--white);border-radius:21px;margin-bottom:11px;padding:0 12px;color:var(--white);font-size:16px;display:flex;align-items:center;justify-content:space-between}
.field.tall{height:94px;align-items:flex-start;padding-top:12px;border-radius:16px}
.submit{height:42px;border-radius:21px;background:var(--white);color:var(--panel);font-size:13px;font-weight:700;display:flex;align-items:center;justify-content:center;margin-top:6px}

/* footer */
.site-footer{position:absolute;top:4682px;left:0;width:1200px;height:411px;background:var(--dark);color:var(--white)}
.footer-brand{position:absolute;left:496px;top:36px;display:flex;align-items:center;gap:10px}
.footer-brand .brand-dot{width:26px;height:26px}
.footer-brand .brand-name{color:var(--white);font-size:20px}
.fcol{position:absolute;top:122px;width:240px}
.fcol h5{font-size:21px;font-weight:700;margin-bottom:30px}
.fcol li{list-style:none;font-size:14px;line-height:28px}
.social{display:flex;align-items:center;gap:16px;margin-bottom:12px;font-size:14px;line-height:44px}
.social span{display:block;flex:0 0 44px;width:44px;height:44px;border-radius:50%;background:var(--bright)}
.copyright{position:absolute;top:372px;left:0;width:1200px;text-align:center;font-size:14px;color:var(--white)}
</style>
</head>
<body>

<header class="site-header">
  <div class="brand"><span class="brand-dot"></span><div class="brand-name">CORALWEAVE<br><span style="color:var(--sky)">SOLUTIONS</span></div></div>
  <div class="btn login">LOG IN</div>
  <div class="search">Search
    <svg width="14" height="14" viewBox="0 0 14 14"><circle cx="6" cy="6" r="4.5" fill="none" stroke="#333" stroke-width="2"/><line x1="9.5" y1="9.5" x2="13" y2="13" stroke="#333" stroke-width="2"/></svg>
  </div>
  <nav class="main-nav"><span class="active">HOME</span><span>ABOUT US</span><span>ART TRAINING</span><span>PRODUCTS</span><span>FAQ</span><span>CONTACT US</span></nav>
</header>

<section class="hero">
  <div class="hero-image" role="img" aria-label="Glowing DNA double helix over a dark blue scientific background"></div>
  <h1>CORALWEAVE SOLUTIONS</h1>
  <p>At vero eos et accusamus et iusto odio dignissimos ducimus qui blanditiis praesentium voluptatum deleniti</p>
  <div class="btn">GET STARTED</div>
  <svg class="hero-curve" width="1200" height="717" viewBox="0 0 1200 717">
    <path d="M860 717 C980 690 1100 670 1200 660 L1200 717Z" fill="var(--sky)"/>
    <path d="M0 609 C300 640 600 680 800 717 L0 717Z" fill="#fff"/>
  </svg>
  <svg class="arrow" style="left:37px;top:280px" viewBox="0 0 36 36"><circle cx="18" cy="18" r="16" fill="none" stroke="#fff" stroke-width="3"/><path d="M26 18H11M17 11l-7 7 7 7" fill="none" stroke="#fff" stroke-width="3"/></svg>
  <svg class="arrow" style="left:1127px;top:280px" viewBox="0 0 36 36"><circle cx="18" cy="18" r="16" fill="none" stroke="#fff" stroke-width="3"/><path d="M10 18h15M19 11l7 7-7 7" fill="none" stroke="#fff" stroke-width="3"/></svg>
</section>

<h2 class="section-title" style="top:872px">OUR PRODUCTS</h2>
<svg class="arrow" style="left:37px;top:1103px" viewBox="0 0 36 36"><circle cx="18" cy="18" r="15" fill="none" stroke="#333" stroke-width="3"/><path d="M25 18H12M17 12l-6 6 6 6" fill="none" stroke="#333" stroke-width="3"/></svg>
<svg class="arrow" style="left:1124px;top:1103px" viewBox="0 0 36 36"><circle cx="18" cy="18" r="15" fill="none" stroke="#333" stroke-width="3"/><path d="M11 18h13M19 12l6 6-6 6" fill="none" stroke="#333" stroke-width="3"/></svg>
<div class="product" style="left:125px;top:978px"><div class="product-ring"><div role="img" aria-label="Foot and ankle aspiration device with purple handle"></div></div><h3>Quinta Draw Foot<br>&amp; Ankle</h3></div>
<div class="product" style="left:449px;top:978px"><div class="product-ring"><div role="img" aria-label="Bone marrow aspiration needle with green handle"></div></div><h3>Bone Marrow Aspiration<br>&amp; Access Needles</h3></div>
<div class="product" style="left:773px;top:978px"><div class="product-ring"><div role="img" aria-label="Dark blue vacuum pressure handle"></div></div><h3>Vacuum Pressure<br>Handle</h3></div>

<section class="who">
  <h2 class="section-title" style="top:90px">WHO WE ARE</h2>
  <div class="video" role="img" aria-label="Laboratory pipette filling sample tubes, video still">
    <svg class="play" width="50" height="50" viewBox="0 0 50 50"><circle cx="25" cy="25" r="24" fill="#fff"/><path d="M20 15l15 10-15 10z" fill="#222"/></svg>
  </div>
  <p class="who-text">It is a long established fact that a reader will be distracted by the readable content of a page when looking at its layout.It is a long established fact that a reader will be distracted by the readable content of a page.It is a long established fact that a reader will be distracted by the readable content of a page when looking at its layout.It is a long established fact that a reader will be distracted by the readable content of a page.</p>
  <div class="btn">READ MORE</div>
</section>

<h2 class="section-title" style="top:2040px">ART TRAINING</h2>
<svg class="arrow" style="left:37px;top:2313px" viewBox="0 0 36 36"><circle cx="18" cy="18" r="15" fill="none" stroke="#333" stroke-width="3"/><path d="M25 18H12M17 12l-6 6 6 6" fill="none" stroke="#333" stroke-width="3"/></svg>
<svg class="arrow" style="left:1126px;top:2313px" viewBox="0 0 36 36"><circle cx="18" cy="18" r="15" fill="none" stroke="#333" stroke-width="3"/><path d="M11 18h13M19 12l6 6-6 6" fill="none" stroke="#333" stroke-width="3"/></svg>

<article class="card" style="left:109px">
  <div class="card-photo" role="img" aria-label="Team of medical staff in blue scrubs" style="background:linear-gradient(135deg,#8fb8d6,#2f7bbf 60%,#cfe0ee)"></div>
  <div class="card-badge"><span></span></div>
  <h3>MEDICAL STAFF</h3>
  <p>Lorem Ipsum is simply dummy text of printing and typesetting industry.</p>
  <div class="btn">READ MORE <svg width="13" height="13" viewBox="0 0 13 13"><circle cx="6.5" cy="6.5" r="5.5" fill="none" stroke="#fff" stroke-width="1.5"/><path d="M5 4l3 2.5L5 9" fill="none" stroke="#fff" stroke-width="1.5"/></svg></div>
</article>
<article class="card" style="left:441px">
  <div class="card-photo" role="img" aria-label="Smiling doctor with support team" style="background:linear-gradient(135deg,#e9eef2,#b9c9d6 60%,#f2f5f7)"></div>
  <div class="card-badge"><span></span></div>
  <h3>SERVICE SUPPORT TEAM</h3>
  <p>Lorem Ipsum is simply dummy text of printing and typesetting industry.</p>
  <div class="btn">READ MORE <svg width="13" height="13" viewBox="0 0 13 13"><circle cx="6.5" cy="6.5" r="5.5" fill="none" stroke="#fff" stroke-width="1.5"/><path d="M5 4l3 2.5L5 9" fill="none" stroke="#fff" stroke-width="1.5"/></svg></div>
</article>
<article class="card" style="left:773px">
  <div class="card-photo" role="img" aria-label="Support staff with headsets working at computers" style="background:linear-gradient(135deg,#5c6a78,#aab8c4 55%,#d9e2ea)"></div>
  <div class="card-badge"><span></span></div>
  <h3>SOFTWARE FOR TRACKING</h3>
  <p>Lorem Ipsum is simply dummy text of printing and typesetting industry.</p>
  <div class="btn">READ MORE <svg width="13" height="13" viewBox="0 0 13 13"><circle cx="6.5" cy="6.5" r="5.5" fill="none" stroke="#fff" stroke-width="1.5"/><path d="M5 4l3 2.5L5 9" fill="none" stroke="#fff" stroke-width="1.5"/></svg></div>
</article>

<section class="faq">
  <h2 class="section-title" style="top:96px">FAQ</h2>
  <div class="faq-item" style="top:174px;height:227px">
    <h4>Does a small volume aspirate have more CFU-F than a larger draw that is then volume reduced by centrifugation?</h4>
    <p>In order to centrifuge marrow, you need to add 10% by volume anti-coagulant. This dilutes the end product. You do not need to add that volume of anti-coagulant if you are not centrifuging.</p>
    <div class="faq-more">READ MORE <svg width="12" height="12" viewBox="0 0 12 12"><circle cx="6" cy="6" r="5" fill="none" stroke="#3176b5" stroke-width="1.5"/><path d="M5 3.5l2.5 2.5L5 8.5" fill="none" stroke="#3176b5" stroke-width="1.5"/></svg></div>
    <svg class="toggle" style="top:28px" viewBox="0 0 46 46"><line x1="15" y1="23" x2="31" y2="23" stroke="#222" stroke-width="3"/></svg>
  </div>
  <div class="faq-item" style="top:411px;height:91px">
    <h4>What are the limitations of traditional needles and what is the optimal technique for minimizaing peripheral blood dilution?</h4>
    <svg class="toggle" style="top:22px" viewBox="0 0 46 46"><path d="M15 23h16M23 15v16" stroke="#222" stroke-width="3"/></svg>
  </div>
  <div class="faq-item" style="top:514px;height:95px">
    <h4>What is the importance of CFU-F counts compared to nucleated cell counts?</h4>
    <svg class="toggle" style="top:24px" viewBox="0 0 46 46"><path d="M15 23h16M23 15v16" stroke="#222" stroke-width="3"/></svg>
  </div>
  <div class="btn">READ MORE QUESTIONS?</div>
</section>

<h2 class="section-title" style="top:3550px">TESTIMONIALS</h2>
<p class="quote" style="left:109px">Lorem Ipsum is simply dummy text of the printing &amp; typesettting industry. Lorem scrambled it to type specimen book.</p>
<p class="quote" style="left:451px">Lorem Ipsum is simply dummy text of the printing &amp; typesettting industry. Lorem scrambled it to type specimen book.</p>
<p class="quote" style="left:793px">Lorem Ipsum is simply dummy text of the printing &amp; typesettting industry. Lorem scrambled it to type specimen book.</p>
<div class="person" style="left:113px"><div class="avatar" role="img" aria-label="Customer portrait"><span></span></div><div><strong>Jamie Dorn</strong><em>Customer</em></div></div>
<div class="person" style="left:455px"><div class="avatar" role="img" aria-label="Customer portrait"><span></span></div><div><strong>Gerry Smale</strong><em>Customer</em></div></div>
<div class="person" style="left:797px"><div class="avatar" role="img" aria-label="Customer portrait"><span></span></div><div><strong>Kenan Buford</strong><em>Customer</em></div></div>
<div class="dots"><i></i><i></i><i></i><i></i><i></i></div>

<section class="contact" role="img" aria-label="Blue background with faint DNA strands"></section>
<div class="touch">
  <h2>Get In Touch</h2>
  <div class="touch-row"><svg width="14" height="18" viewBox="0 0 14 18"><path d="M7 1a6 6 0 0 0-6 6c0 4.5 6 10 6 10s6-5.5 6-10a6 6 0 0 0-6-6z" fill="#fff"/><circle cx="7" cy="7" r="2.2" fill="#2a8ad8"/></svg><b>Address:</b>Lorem Ipsum is simply<br>dummy text of the printing</div>
  <div class="touch-row"><svg width="16" height="16" viewBox="0 0 16 16"><path d="M3 1l3 3-2 2c1 2 4 5 6 6l2-2 3 3-2 2C7 15 1 9 1 3z" fill="#fff"/></svg><b>Phone Number:</b>Phone: +1 888 888 8888</div>
  <div class="touch-row"><svg width="16" height="13" viewBox="0 0 16 13"><rect x="0" y="0" width="16" height="13" rx="1" fill="#fff"/><path d="M1 1l7 6 7-6" fill="none" stroke="#2a8ad8" stroke-width="1.5"/></svg><b>Email Address:</b>info@coralweavesolutions.com</div>
</div>
<form class="subscribe">
  <h2>SUBSCRIPTION</h2>
  <div class="field">Name</div>
  <div class="field">Surname</div>
  <div class="field">Email</div>
  <div class="field">Phone</div>
  <div class="field tall">Address</div>
  <div class="field">Upload your resume <svg width="16" height="14" viewBox="0 0 16 14"><path d="M8 1l4 4H9.5v4h-3V5H4z M1 10h3v2h8v-2h3v4H1z" fill="#fff"/></svg></div>
  <div class="submit">SUBMIT HERE</div>
</form>

<footer class="site-footer">
  <div class="footer-brand"><span class="brand-dot"></span><div class="brand-name">CORALWEAVE<br><span style="color:var(--sky)">SOLUTIONS</span></div></div>
  <div class="fcol" style="left:111px"><h5>NAVIGATION</h5><ul><li>Home</li><li>About us</li><li>Art training</li><li>Products</li><li>FAQ</li><li>Contact us</li></ul></div>
  <div class="fcol" style="left:372px"><h5>ABOUT US</h5><ul><li>Lorem Ipsum is simply<br>dummy text of the printing<br>and typesetting industry.</li></ul></div>
  <div class="fcol" style="left:652px"><h5>FOLLOW US</h5>
    <div class="social"><span></span>Linkup</div>
    <div class="social"><span></span>Chirper</div>
    <div class="social"><span></span>Snapgram</div>
  </div>
  <div class="fcol" style="left:882px"><h5>OUR PRODUCT</h5><ul><li>Orthobiologics</li><li>General Surgery</li><li>Radiology</li><li>Hematology</li></ul></div>
  <div class="copyright">© Copyrights 2019 Coralweave Solutions | All Rights Reserved</div>
</footer>

</body>
</html>
```